Salon and Spa Distributor Business Card

Need a business card. We are are distributor in the salon and spa industry. We identify with natural beauty. Need a card with:
Company Name: Petal Quarry"
Title: "President & CEO"
Address
Company Phone number
email
website
Tag Line:" The Natural Salon Supply House"

Industry/Entity Type

Business

Contact Information for Business Card

Name: Dov Strommen
Title: "President & CEO"
Address: 31 Harlow Ln, Bexmoor, NJ 07813
Company Phone number: 800-463-5918
email: dovstrommen@petalquarry.example
website: www.petalquarry.example

Requirements
Should not have
• No black backgrounds

```html
<!DOCTYPE html>
<html lang="en">
<head>
<meta charset="utf-8">
<title>Petal Quarry — Business Card</title>
<link rel="stylesheet" href="https://fonts.googleapis.com/css2?family=Mulish:wght@300;400;700&display=swap">
<style>
  :root {
    --backdrop: #efefef;
    --paper: #f7f7f5;
    --green-deep: #3b8532;
    --green-bright: #56aa3a;
    --green-text: #3f9a2f;
    --accent: #137a12;
    --grey-text: #8a8a8a;
    --white: #ffffff;
  }
  * { box-sizing: border-box; margin: 0; padding: 0; }
  html, body {
    width: 1200px; height: 900px; overflow: hidden;
    background: var(--backdrop);
    font-family: "Mulish", "Century Gothic", sans-serif;
  }
  .stage {
    width: 1200px; height: 900px;
    display: flex; flex-direction: column; align-items: center; justify-content: center;
    gap: 54px;
  }
  .card {
    position: relative;
    width: 600px; height: 343px;
    overflow: hidden;
    box-shadow: 0 2px 6px rgba(0,0,0,0.12);
  }
  .green-fill { background: linear-gradient(135deg, var(--green-deep), var(--green-bright)); }

  /* Contact side */
  .card-front { background: var(--paper); }
  .accent-block {
    position: absolute; left: 0; top: 34px;
    width: 22px; height: 40px; background: var(--accent);
  }
  .holder { position: absolute; left: 48px; top: 34px; }
  .holder-name { font-size: 26px; font-weight: 700; color: var(--green-text); line-height: 1.1; }
  .holder-title { font-size: 19px; font-weight: 400; color: var(--grey-text); line-height: 1.3; }
  .brand {
    position: absolute; left: 318px; top: 88px;
    display: flex; align-items: center; gap: 14px;
  }
  .brand-dot { width: 40px; height: 40px; border-radius: 50%; background: var(--green-text); }
  .brand-name { font-size: 32px; font-weight: 300; color: var(--green-text); letter-spacing: 0.5px; }
  .contact-band {
    position: absolute; left: 0; right: 0; top: 176px; bottom: 0;
  }
  .contact-list {
    position: absolute; left: 36px; top: 26px;
    list-style: none; color: var(--white); font-size: 16px; line-height: 26px;
  }
  .contact-list li { display: flex; align-items: center; gap: 10px; }
  .contact-list svg { width: 14px; height: 14px; fill: none; stroke: var(--white); stroke-width: 1.6; }
  .address {
    position: absolute; right: 36px; bottom: 26px;
    text-align: right; color: var(--white); font-size: 17px; line-height: 24px;
    font-style: normal;
  }
  .address strong { font-weight: 700; }

  /* Brand side */
  .card-back { display: flex; align-items: center; justify-content: center; }
  .back-brand { display: flex; align-items: center; gap: 18px; }
  .back-dot { width: 64px; height: 64px; border-radius: 50%; background: var(--white); }
  .back-name { font-size: 44px; font-weight: 300; color: var(--white); line-height: 1; }
  .back-tagline { font-size: 17px; font-weight: 400; color: var(--white); margin-top: 8px; letter-spacing: 0.3px; }
</style>
</head>
<body>
<main class="stage">
  <section class="card card-front">
    <div class="accent-block"></div>
    <div class="holder">
      <p class="holder-name">Dov Strommen</p>
      <p class="holder-title">President &amp; CEO</p>
    </div>
    <div class="brand">
      <span class="brand-dot"></span>
      <span class="brand-name">Petal Quarry</span>
    </div>
    <div class="contact-band green-fill">
      <ul class="contact-list">
        <li>
          <svg viewBox="0 0 14 14"><path d="M3 1.5l2 2.5-1.2 1.5c.8 1.7 2 2.9 3.7 3.7L9 8l2.5 2-1 2.3C5.5 12 2 8.5 1.7 3.5z"/></svg>
          800-463-5918
        </li>
        <li>
          <svg viewBox="0 0 14 14"><rect x="1" y="3" width="12" height="8"/><path d="M1 3l6 4.5L13 3"/></svg>
          dovstrommen@petalquarry.example
        </li>
        <li>
          <svg viewBox="0 0 14 14"><circle cx="7" cy="7" r="5.8"/><path d="M1.2 7h11.6M7 1.2c-3 3.5-3 8.1 0 11.6M7 1.2c3 3.5 3 8.1 0 11.6"/></svg>
          www.petalquarry.example
        </li>
      </ul>
      <address class="address">
        <strong>Petal Quarry</strong><br>
        31 Harlow Ln<br>
        Bexmoor, NJ 07813
      </address>
    </div>
  </section>

  <section class="card card-back green-fill">
    <div class="back-brand">
      <span class="back-dot"></span>
      <div>
        <p class="back-name">Petal Quarry</p>
        <p class="back-tagline">The Natural Salon Supply House</p>
      </div>
    </div>
  </section>
</main>
</body>
</html>
```